Coastline Premier Retreats Business Card Design

Design a business card for Coastline Premier Retreats. Look at the website for colors and reference. Card should have logo, name, title, office number, mobile number, email, URL and a tagline like, "Luxury Hotel & Resort Email Marketing" (This might change).

https://www.coastlinepremierretreats.example

The rest I will leave up to your imagination.

Contact Information for Business Card

Logo, name, title, office number, mobile number, email, URL and a tagline like, "Luxury Hotel & Resort Email Marketing" (This might change).

```html
<!DOCTYPE html>
<html lang="en">
<head>
<meta charset="utf-8">
<title>Coastline Premier Retreats – Business Card</title>
<link rel="stylesheet" href="https://fonts.googleapis.com/css2?family=Open+Sans:wght@400;600;700;800&display=swap">
<style>
  :root {
    --page: #2a2a2d;
    --card-dark: #232226;
    --accent: #f37021;
    --ink-light: #ffffff;
    --ink-dark: #111111;
    --sky: #b7d3e8;
    --sea: #5fb8b5;
    --foliage: #7f9a5a;
    --rock: #9a9384;
  }
  * { box-sizing: border-box; margin: 0; padding: 0; }
  html, body {
    width: 1200px; height: 780px; overflow: hidden;
    background: var(--page);
    font-family: "Open Sans", Arial, sans-serif;
  }
  .canvas { position: relative; width: 1200px; height: 780px; }

  .card {
    position: absolute;
    width: 560px; height: 320px;
    overflow: hidden;
    box-shadow: 0 18px 40px rgba(0,0,0,.45);
  }

  /* Front */
  .card--front { left: 50px; top: 60px; }
  .front-photo {
    position: absolute; inset: 0;
    background:
      linear-gradient(160deg, var(--sky) 0%, #cfe0ea 22%, transparent 40%),
      linear-gradient(115deg, var(--foliage) 0%, #a7b98a 30%, var(--sea) 55%, #7cc6c0 70%, var(--foliage) 90%, var(--rock) 100%);
    opacity: .85;
  }
  .front-brand {
    position: absolute; left: 0; right: 0; top: 50%;
    transform: translateY(-50%);
    display: flex; align-items: center; justify-content: center; gap: 14px;
    font-weight: 800; font-size: 34px; letter-spacing: .5px;
    text-transform: uppercase; color: var(--ink-dark);
    text-align: center; line-height: 1.1;
  }
  .brand-square { width: 18px; height: 18px; background: var(--accent); flex: none; }

  /* Back */
  .card--back { left: 590px; top: 400px; background: var(--card-dark); }
  .tagline-band {
    position: absolute; left: 0; top: 0; bottom: 0; width: 108px;
    background: var(--accent);
    display: flex; align-items: center; justify-content: center;
  }
  .tagline {
    writing-mode: vertical-rl; transform: rotate(180deg);
    color: var(--ink-light); font-size: 17px; font-weight: 400;
    line-height: 1.35; text-align: center;
  }
  .back-brand {
    position: absolute; right: 70px; top: 34px;
    display: flex; align-items: center; gap: 10px;
    font-weight: 800; font-size: 21px; text-transform: uppercase;
    color: var(--ink-light); letter-spacing: .3px;
  }
  .name-tab {
    position: absolute; right: 0; top: 110px; width: 22px; height: 52px;
    background: var(--accent);
  }
  .person { position: absolute; right: 36px; top: 108px; text-align: right; }
  .person-name { font-size: 28px; font-weight: 700; line-height: 1.1; }
  .person-name .first { color: var(--accent); }
  .person-name .last { color: var(--ink-light); }
  .person-title { color: var(--ink-light); font-size: 14px; font-weight: 600; margin-top: 2px; }

  .contacts {
    position: absolute; right: 24px; top: 192px;
    list-style: none; text-align: right;
  }
  .contacts li {
    display: flex; justify-content: flex-end; align-items: center; gap: 9px;
    color: var(--ink-light); font-size: 13px; line-height: 22px;
  }
  .contacts svg { width: 13px; height: 13px; flex: none; }
</style>
</head>
<body>
<main class="canvas">

  <section class="card card--front" aria-label="Business card front">
    <div class="front-photo" role="img" aria-label="Photograph of a rocky coastline with cypress trees and turquoise sea"></div>
    <div class="front-brand">
      <span class="brand-square"></span>
      <span>Coastline Premier Retreats</span>
    </div>
  </section>

  <section class="card card--back" aria-label="Business card back">
    <div class="tagline-band">
      <p class="tagline">Luxury Hotel &amp;<br>Resort Email Marketing</p>
    </div>

    <div class="back-brand">
      <span class="brand-square"></span>
      <span>Coastline Premier Retreats</span>
    </div>

    <div class="name-tab"></div>
    <div class="person">
      <p class="person-name"><span class="first">Marta</span> <span class="last">Velinska</span></p>
      <p class="person-title">Co-Founder</p>
    </div>

    <ul class="contacts">
      <li>(555) 014-2758
        <svg viewBox="0 0 16 16" aria-hidden="true"><path fill="var(--accent)" d="M3.5 1h3l1.2 3.5-1.9 1.3a8 8 0 0 0 4.4 4.4l1.3-1.9L15 9.5v3c0 1-1 2-2 1.9C6.6 14 2 9.4 1.6 3 1.5 2 2.5 1 3.5 1z"/></svg>
      </li>
      <li>(555) 018-7777
        <svg viewBox="0 0 16 16" aria-hidden="true"><rect x="4" y="1" width="8" height="14" rx="1.5" fill="none" stroke="var(--accent)" stroke-width="1.6"/><circle cx="8" cy="12.5" r=".9" fill="var(--accent)"/></svg>
      </li>
      <li>www.coastlinepremierretreats.example
        <svg viewBox="0 0 16 16" aria-hidden="true"><circle cx="8" cy="8" r="6.5" fill="none" stroke="var(--accent)" stroke-width="1.5"/><ellipse cx="8" cy="8" rx="2.8" ry="6.5" fill="none" stroke="var(--accent)" stroke-width="1.2"/><path d="M1.5 8h13" stroke="var(--accent)" stroke-width="1.2"/></svg>
      </li>
      <li>info@coastlinepremierretreats.example
        <svg viewBox="0 0 16 16" aria-hidden="true"><rect x="1.5" y="3.5" width="13" height="9" fill="none" stroke="var(--accent)" stroke-width="1.5"/><path d="M1.5 3.5 8 9l6.5-5.5" fill="none" stroke="var(--accent)" stroke-width="1.5"/></svg>
      </li>
    </ul>
  </section>

</main>
</body>
</html>
```